TWPC Business Card Design

Business card for sole operator professional civil and traffic engineer.
Clients are developers and planners who require assistance with traffic strategic master planning advice and design development for access and infrastructure associated with the development.
Colours already in use are greens for the business name and black for other legend. The attached file shows the letterhead template which is currently in use.
Target Market(s)
Professional Clients in development industry
Most clients known to the Principal and card is mostly required to allow ongoing contact
Industry/Entity Type
Business
Contact Information for Business Card
LACHLAN PETTIGREW CONSULTING PARTNERS
ABN 37 814 529 106
PO Box 418 KELWOOD NSW 2619
Lachlan Pettigrew 0412 358 971
l.pettigrew@corvanmail.net

```html
<!DOCTYPE html>
<html lang="en">
<head>
<meta charset="utf-8">
<title>TWPC Business Card</title>
<link rel="stylesheet" href="https://fonts.googleapis.com/css2?family=Arimo:wght@400&display=swap">
<style>
  :root {
    --page-bg: #f2f2f2;
    --card-black: #050505;
    --band-green: #9ccc3c;
    --text-green: #a6d44a;
    --text-black: #0a0a0a;
  }
  * { margin: 0; padding: 0; box-sizing: border-box; }
  html, body {
    width: 1200px;
    height: 864px;
    overflow: hidden;
    background: var(--page-bg);
    font-family: "Arimo", Arial, sans-serif;
  }
  .canvas {
    position: relative;
    width: 1200px;
    height: 864px;
  }
  .business-card {
    position: absolute;
    left: 100px;
    top: 146px;
    width: 1000px;
    height: 572px;
    background: var(--card-black);
    box-shadow: 0 10px 30px rgba(0,0,0,0.18);
    overflow: hidden;
  }
  .business-name {
    position: absolute;
    left: 88px;
    right: 60px;
    top: 98px;
    font-size: 34px;
    font-weight: 400;
    letter-spacing: 0;
    color: var(--text-green);
    white-space: nowrap;
    text-align: right;
  }
  .name-band {
    position: absolute;
    left: 0;
    top: 186px;
    width: 100%;
    height: 116px;
    background: var(--band-green);
  }
  .person-name {
    position: absolute;
    left: 88px;
    bottom: 18px;
    font-size: 30px;
    color: var(--text-black);
    white-space: nowrap;
  }
  .abn {
    position: absolute;
    right: 66px;
    top: 14px;
    font-size: 25px;
    color: var(--text-black);
    white-space: nowrap;
  }
  .contact-list {
    position: absolute;
    right: 52px;
    top: 340px;
    list-style: none;
  }
  .contact-item {
    display: flex;
    justify-content: flex-end;
    align-items: center;
    gap: 22px;
    height: 46px;
    font-size: 25px;
    color: var(--text-green);
    white-space: nowrap;
  }
  .contact-icon {
    width: 26px;
    height: 26px;
    fill: var(--text-green);
    flex: none;
  }
</style>
</head>
<body>
<main class="canvas">
  <section class="business-card" aria-label="Business card front">
    <h1 class="business-name">LACHLAN PETTIGREW CONSULTING PARTNERS</h1>
    <div class="name-band">
      <p class="abn">ABN 37 814 529 106</p>
      <p class="person-name">LACHLAN PETTIGREW</p>
    </div>
    <ul class="contact-list">
      <li class="contact-item">
        <span>0412 358 971</span>
        <svg class="contact-icon" viewBox="0 0 24 24" aria-hidden="true">
          <path d="M2 8c0-3 5-5 10-5s10 2 10 5v2h-5V8c-1-1-3-1.5-5-1.5S8 7 7 8v2H2z"/>
          <path d="M6 11h12l3 9H3zM12 13.5a3 3 0 1 0 0 6 3 3 0 0 0 0-6z"/>
        </svg>
      </li>
      <li class="contact-item">
        <span>l.pettigrew@corvanmail.net</span>
        <svg class="contact-icon" viewBox="0 0 24 24" aria-hidden="true">
          <path d="M2 5h20v14H2z"/>
          <path d="M2 5l10 8 10-8v1.6l-10 8-10-8z" fill="#050505"/>
        </svg>
      </li>
      <li class="contact-item">
        <span>418 KELWOOD NSW 2619</span>
        <svg class="contact-icon" viewBox="0 0 24 24" aria-hidden="true">
          <path d="M12 1a8 8 0 0 0-8 8c0 6 8 14 8 14s8-8 8-14a8 8 0 0 0-8-8zm0 4.5a3.5 3.5 0 1 1 0 7 3.5 3.5 0 0 1 0-7z" fill-rule="evenodd"/>
        </svg>
      </li>
    </ul>
  </section>
</main>
</body>
</html>
```